Robotic Physical Therapy office needs a Grand Opening Flyer

We need a Grand Opening flyer design for a robotic physical therapy office named Kinetic Harbor Wellness. We would like it to have a clean, classy, upscale feeling that gives potential clients a V.I.P. feeling. We would like to use the colors black, gray, and yellow (logo will be uploaded).

Event: Thursday, June 1st, 2023 from 12pm-6pm
location: 58274 Pellham Ave, Bloomfield Hills, MI 48519

Industry/Entity Type

Physical therapy

Font styles to use
Script

Colors

Designer to choose colors to be used in the design.

Requirements
Nice to have
• More of a vip feel for the invite

```html
<!DOCTYPE html>
<html lang="en">
<head>
<meta charset="utf-8">
<title>Kinetic Harbor Wellness — Grand Opening Flyer</title>
<link rel="stylesheet" href="https://fonts.googleapis.com/css2?family=Montserrat:wght@500;800&family=Poppins:wght@300;400;500;600;700;800&display=swap">
<style>
  :root {
    --ink: #000000;
    --paper: #ffffff;
    --gold: #f6d832;
    --amber: #e2a63a;
    --grey: #8a8a8a;
    --rule: #6d6d6d;
    --bg: #ffffff;
  }
  * { margin: 0; padding: 0; box-sizing: border-box; }
  html, body { width: 1200px; height: 1200px; overflow: hidden; background: var(--bg); }
  .flyer {
    position: absolute; left: 222px; top: 66px; width: 755px; height: 1067px;
    background: var(--ink); overflow: hidden; color: var(--paper);
    font-family: "Poppins", sans-serif;
  }
  .sparkle-field {
    position: absolute; left: 0; top: 0; width: 100%; height: 520px;
    background:
      radial-gradient(ellipse 60% 22% at 50% 0%, rgba(226,166,58,.35), transparent 70%),
      radial-gradient(ellipse 18% 50% at 100% 45%, rgba(226,166,58,.25), transparent 70%),
      radial-gradient(ellipse 12% 40% at 0% 40%, rgba(226,166,58,.18), transparent 70%);
  }
  .glitter-floor {
    position: absolute; left: 0; bottom: 19px; width: 100%; height: 240px;
    background: linear-gradient(180deg, rgba(0,0,0,0) 0%, rgba(90,90,90,.45) 45%, rgba(120,120,120,.55) 70%, rgba(40,40,40,.7) 100%);
  }
  .gold-band {
    position: absolute; left: 0; bottom: 0; width: 100%; height: 19px;
    background: linear-gradient(90deg, #6b5a12, var(--gold) 45%, #8a7418);
  }
  .brand {
    position: absolute; left: 256px; top: 95px; height: 90px;
    display: flex; align-items: center; gap: 10px;
  }
  .brand-dot { width: 62px; height: 62px; border: 3px solid var(--paper); border-radius: 50%; flex: none; }
  .brand-name {
    font-family: "Poppins", sans-serif; font-weight: 600; color: var(--paper);
    font-size: 22px; line-height: 1.1; letter-spacing: .5px;
  }
  .headline-grand {
    position: absolute; left: 0; width: 100%; top: 184px; text-align: center;
    font-family: "Montserrat", sans-serif; font-weight: 800; font-size: 166px;
    line-height: 1; color: var(--gold); letter-spacing: -3px;
  }
  .headline-opening {
    position: absolute; left: 0; width: 100%; top: 329px; text-align: center;
    font-family: "Montserrat", sans-serif; font-weight: 500; font-size: 113px;
    line-height: 1; color: var(--paper); letter-spacing: -2px;
  }
  .rule { position: absolute; left: 76px; width: 596px; height: 1px; background: var(--rule); }
  .rule-top { top: 460px; }
  .rule-bottom { top: 522px; }
  .service {
    position: absolute; left: 0; width: 100%; top: 474px; text-align: center;
    font-size: 30px; font-weight: 400; letter-spacing: 6px; line-height: 34px;
  }
  .event-label {
    position: absolute; left: 76px; width: 596px; top: 546px;
    display: flex; align-items: center; gap: 8px;
    color: var(--gold); font-size: 43px; font-weight: 400; letter-spacing: 12px; line-height: 44px;
  }
  .event-label::before, .event-label::after { content: ""; flex: 1; height: 1px; background: var(--gold); }
  .event-label span { margin-right: -12px; }
  .event-date {
    position: absolute; left: 0; width: 100%; top: 598px; text-align: center;
    font-size: 47px; line-height: 52px; font-weight: 800; letter-spacing: -1px; white-space: nowrap;
  }
  .event-date .year { font-weight: 300; }
  .event-time {
    position: absolute; left: 191px; top: 657px; width: 372px; height: 53px;
    background: var(--gold); border-radius: 16px; color: #1a1a1a;
    display: flex; align-items: center; justify-content: center;
    font-size: 30px; letter-spacing: 2px; font-weight: 400;
  }
  .event-time b { font-weight: 700; margin-left: 12px; }
  .pin { position: absolute; left: 346px; top: 722px; width: 62px; height: 62px; }
  .address {
    position: absolute; left: 0; width: 100%; top: 794px; text-align: center;
    font-size: 28px; line-height: 34px; font-weight: 600;
  }
</style>
</head>
<body>
  <main class="flyer">
    <div class="sparkle-field" role="img" aria-label="Golden bokeh lights and sparkling stars hanging from the top"></div>
    <div class="glitter-floor" role="img" aria-label="Silver glitter scattered across a dark floor"></div>
    <div class="gold-band"></div>

    <div class="brand">
      <div class="brand-dot"></div>
      <div class="brand-name">KINETIC HARBOR<br>WELLNESS</div>
    </div>

    <h1 class="headline-grand">GRAND</h1>
    <h2 class="headline-opening">OPENING</h2>

    <div class="rule rule-top"></div>
    <p class="service">ROBOTIC PHYSICAL THERAPY</p>
    <div class="rule rule-bottom"></div>

    <p class="event-label"><span>EVENT</span></p>
    <p class="event-date">THURSDAY JUNE 1ST, <span class="year">2023</span></p>
    <p class="event-time">FROM<b>12PM-6PM</b></p>

    <svg class="pin" viewBox="0 0 62 62" aria-hidden="true">
      <circle cx="31" cy="31" r="31" fill="var(--gold)"/>
      <path d="M31 16c-6.6 0-11 4.8-11 10.6 0 7.6 11 19.4 11 19.4s11-11.8 11-19.4C42 20.8 37.6 16 31 16z" fill="#111"/>
      <circle cx="31" cy="26.5" r="3.6" fill="var(--gold)"/>
    </svg>

    <p class="address">58274 Pellham Ave,<br>Bloomfield Hills, MI 48519</p>
  </main>
</body>
</html>
```